Under Morning Lantern website

I need a website to sell my t-shirt designs. I have around 5 designs I plan to sell on my initial launch, but only 3 photos at the moment. I would love a main page with the product images below maybe a large nicely designed header image, showing products with their sizes, item name/description, a way to add to cart and a review system like stars below each product image. Maybe a share option to Gallery, Facebook, Twitter, Pinterest, etc. would be cool too. Also on the main page under the product images a section showcasing my Gallery photos for the company. Then a section where I will include an About Me video from like YouTube. Lastly, on the main page an option to join my Mailing List at the footer with links to my Facebook and Gallery social accounts, links to pages (About Me, Shop, Gallery page, & Contact Us) as well as Track Order.

The other 4 pages will be for an About Me, which is the video I will make later that will be from YouTube. Then the Shop page. Then the Gallery page showcasing all the photos I plan to use to market the products, and a Contact Us Page.

I plan to possibly connect this to Shopify, so showcasing payment options (Palo, Birch Pay, Wayfarer, etc.) would be nice.

Lastly, I don't plan on doing returns/exchanges so maybe an area showing that would be nice too. ALL SALES FINAL

Mobile Friendly!

1st image is logo and other 4 images are t-shirt designs

Coded - Design and coding required

5+ page

• Separate pages, No Refunds (All Sales Final), Add to Cart, Way to Purchase

```html
<!DOCTYPE html>
<html lang="en">
<head>
<meta charset="utf-8">
<title>Under Morning Lantern – Product</title>
<link href="https://fonts.googleapis.com/css2?family=Poppins:wght@300;400;500;600;700&family=Roboto:wght@400;500;700;900&display=swap" rel="stylesheet">
<style>
:root{
  --blue:#00aeef;
  --grey-band:#d4d7dd;
  --ink:#1b1b1b;
  --text:#555;
  --muted:#999;
  --star:#f7941d;
  --green:#5a9d0a;
  --panel:#f5f5f5;
  --footer:#2b2b2b;
  --footer-bottom:#222;
  --dark-btn:#3a3a3a;
  --hover-card:#eef7fc;
}
*{box-sizing:border-box;margin:0;padding:0}
html,body{width:1200px;height:2221px;overflow:hidden}
body{position:relative;font-family:"Poppins",sans-serif;color:var(--ink);background:#fff}
.abs{position:absolute}
a{color:inherit;text-decoration:none}

/* header */
.hero{left:0;top:0;width:1200px;height:314px;background:linear-gradient(90deg,var(--blue) 50%,var(--grey-band) 50%)}
.brand{left:118px;top:40px;font-family:"Roboto",sans-serif;font-weight:900;font-size:23px;line-height:26px;color:#000;width:200px}
.nav{left:355px;top:44px;width:635px;height:44px;background:#fff;border-radius:22px;display:flex;align-items:center;font-family:"Roboto",sans-serif;font-size:17px;overflow:hidden}
.nav a{margin-left:46px}
.nav a:first-child{margin-left:46px}
.nav .active{color:var(--blue);position:relative}
.nav .active::after{content:"";position:absolute;left:50%;bottom:-8px;width:4px;height:4px;border-radius:50%;background:var(--blue)}
.nav .track{margin-left:auto;width:170px;height:44px;background:var(--blue);color:#fff;display:flex;align-items:center;justify-content:center;border-radius:22px}
.cart{left:1048px;top:48px}
.page-title{left:0;width:1200px;top:196px;text-align:center;font-family:"Roboto",sans-serif;font-weight:700;font-size:34px;color:#000}
.crumbs{left:0;width:1200px;top:246px;text-align:center;font-family:"Roboto",sans-serif;font-size:15px;color:#000;word-spacing:2px}

/* gallery */
.thumb{left:118px;width:67px;height:76px;background:var(--panel)}
.thumb.sel{border:2px solid var(--blue)}
.thumb i{position:absolute;left:14px;top:14px;width:37px;height:44px;background:#e6e6e6;border-radius:4px}
.stage{left:194px;top:372px;width:485px;height:455px;background:var(--panel)}
.stage .label{position:absolute;left:26px;top:22px;color:var(--blue);font-size:14px}
.shirt-art{position:absolute;left:72px;top:46px;width:332px;height:360px;border-radius:40px 40px 8px 8px;background:radial-gradient(circle at 50% 30%,#d8d8d8 0 18%,#e9e9e9 19%)}

/* buy box */
.p-name{left:726px;top:366px;font-size:31px;font-weight:500}
.stars{color:var(--star);letter-spacing:1px}
.rating{left:726px;top:415px;font-size:13px;color:var(--text)}
.price{left:726px;top:443px;font-size:29px;font-weight:400}
.lede{left:726px;top:486px;width:345px;font-size:12.5px;line-height:25px;color:var(--text);font-weight:300}
.opt-label{left:726px;font-size:13px;font-weight:500;color:#444}
.swatch{top:567px;width:19px;height:19px;border-radius:50%}
.size{top:618px;display:flex;align-items:center;gap:8px;font-size:13px;color:#555;font-weight:500}
.size b{display:inline-block;width:21px;height:21px;border:1px solid #ccc;border-radius:50%}
.clear{left:850px;top:652px;font-size:11.5px;color:var(--muted)}
.qty{left:726px;top:689px;width:57px;height:33px;border:1px solid #ccc;font-size:13px;color:var(--blue);padding:8px 0 0 16px}
.qty span{position:absolute;right:0;width:18px;height:16px;border-left:1px solid #ccc;font-size:10px;color:#444;text-align:center;line-height:15px}
.btn{display:flex;align-items:center;justify-content:center;font-size:14px;font-weight:500;color:#fff}
.add{left:792px;top:689px;width:190px;height:33px;background:var(--blue)}
.buy{left:726px;top:741px;width:255px;height:33px;background:var(--dark-btn)}
.share{left:726px;top:795px;width:144px;height:33px;border:1px solid #ccc;display:flex;align-items:center;justify-content:space-around;padding:0 14px}
.share i{width:7px;height:7px;border-radius:50%;background:#777}

/* tabs & reviews */
.tab{top:890px;font-size:27px;font-weight:600}
.tab.off{color:#c9c9c9}
.h-sm{font-size:15px;font-weight:500;color:#222}
.score{left:121px;top:983px;font-size:26px;color:var(--green);font-weight:500}
.score small{font-size:12px;color:#444;margin-left:6px;font-weight:400}
.row{left:121px;width:500px;height:14px;font-size:12px}
.row .stars{position:absolute;left:0;top:-4px;font-size:13px}
.row .bar{position:absolute;left:106px;top:2px;width:352px;height:10px;background:#eee}
.row .fill{height:100%;background:var(--green)}
.row .pct{position:absolute;left:469px;top:-1px;color:var(--muted)}
.note{left:658px;top:987px;font-size:12px;color:#444}
.note a{color:#e8505b}
.avatar{left:126px;top:1268px;width:52px;height:52px;border-radius:50%;background:#ccc}
.review-body{left:198px;top:1322px;width:860px;font-size:12.5px;line-height:25px;color:#777;font-weight:300}

/* related */
.related{left:0;width:1200px;top:1437px;text-align:center;font-size:33px;font-weight:500}
.card{top:1522px;width:220px;height:323px;border:1px solid #e6e6e6;background:#fff}
.card.hover{background:var(--hover-card);border-color:var(--blue)}
.card .art{position:absolute;left:30px;top:34px;width:160px;height:165px;border-radius:16px 16px 4px 4px}
.card .nm{position:absolute;left:34px;top:228px;font-size:16px;font-weight:600}
.card .stars{position:absolute;left:34px;top:254px;font-size:13px}
.card .pr{position:absolute;left:34px;top:276px;font-size:17px;font-weight:600}
.ring{position:absolute;right:16px;width:41px;height:41px;border-radius:50%;border:2px solid var(--blue);background:#fff}
.ring.solid{background:var(--blue)}

/* footer */
.foot{left:0;top:1930px;width:1200px;height:216px;background:var(--footer)}
.foot-bottom{left:0;top:2146px;width:1200px;height:75px;background:var(--footer-bottom)}
.f-txt{color:#c8c8c8;font-size:13.5px;line-height:26px}
.f-head{color:#fff;font-size:15.5px}
.vline{top:1975px;width:1px;height:140px;background:#444}
.final{left:118px;top:1968px;color:var(--blue);font-size:13px;line-height:27px}
.email-box{left:513px;top:2038px;width:364px;height:38px;border-radius:19px;background:#e9ecef;overflow:hidden;font-size:14px;color:#777}
.email-box span{position:absolute;left:26px;top:10px}
.email-box b{position:absolute;right:0;top:0;width:119px;height:38px;background:var(--blue);color:#fff;font-weight:600;display:flex;align-items:center;justify-content:center;border-radius:19px}
.socials{left:522px;top:2095px;display:flex;gap:18px}
.socials i{width:12px;height:12px;border-radius:50%;background:#9a9a9a}
.f-brand{left:944px;top:1970px;font-family:"Roboto",sans-serif;font-weight:900;font-size:17px;color:var(--blue);width:150px;text-align:center;line-height:20px}
.f-track{left:952px;top:2036px;width:135px;height:38px;background:var(--blue);color:#fff;font-size:14px}
.copy{left:120px;top:2172px;font-size:13.5px;color:#9a9a9a}
.pay{top:2167px;width:49px;height:30px;background:#fff;border-radius:2px;font-size:10px;font-weight:600;color:#333;display:flex;align-items:center;justify-content:center}
</style>
</head>
<body>

<header>
  <div class="abs hero"></div>
  <div class="abs brand">Under Morning Lantern</div>
  <nav class="abs nav">
    <a href="#">About</a><a href="#" class="active">Shop</a><a href="#">Gallery</a><a href="#">Contact</a>
    <a href="#" class="track">Track Order</a>
  </nav>
  <svg class="abs cart" width="30" height="36" viewBox="0 0 30 36" aria-label="Cart">
    <path d="M2 12h4l3 13h14l3-9H8" fill="none" stroke="#666" stroke-width="1.6"/>
    <circle cx="11" cy="29" r="2" fill="none" stroke="#666" stroke-width="1.4"/>
    <circle cx="21" cy="29" r="2" fill="none" stroke="#666" stroke-width="1.4"/>
    <circle cx="23" cy="7" r="7" fill="#00aeef"/>
    <text x="23" y="10.5" font-size="10" fill="#fff" text-anchor="middle" font-family="Roboto,sans-serif">0</text>
  </svg>
  <h1 class="abs page-title">PRODUCT NAME</h1>
  <div class="abs crumbs">Home &nbsp;&nbsp;| &nbsp;&nbsp;Shop &nbsp;&nbsp;| &nbsp;&nbsp;Product Name</div>
</header>

<section class="product">
  <div class="abs thumb" style="top:372px"><i></i></div>
  <div class="abs thumb sel" style="top:457px"><i></i></div>
  <div class="abs stage">
    <span class="label">Back Design</span>
    <div class="shirt-art" role="img" aria-label="White t-shirt, back view, with a layered heart print"></div>
  </div>

  <h2 class="abs p-name">Product Name</h2>
  <div class="abs rating"><span class="stars">★★★★☆</span> (18 customer review)</div>
  <div class="abs price">$99</div>
  <p class="abs lede">Lorem Ipsum is simply dummy text of the printing and typesetting industry. Lorem Ipsum has been the industry's</p>

  <div class="abs opt-label" style="top:567px">COLOR</div>
  <svg class="abs" style="left:806px;top:566px" width="20" height="20"><circle cx="10" cy="10" r="10" fill="#9b59b6"/><path d="M5.5 10l3 3 6-6" stroke="#fff" stroke-width="1.6" fill="none"/></svg>
  <div class="abs swatch" style="left:843px;background:#222"></div>
  <div class="abs swatch" style="left:881px;border:1px solid #ccc"></div>
  <div class="abs swatch" style="left:917px;background:var(--blue)"></div>
  <div class="abs swatch" style="left:954px;background:#26b3a8"></div>

  <div class="abs opt-label" style="top:620px">SIZE</div>
  <div class="abs size" style="left:806px"><svg width="22" height="22"><circle cx="11" cy="11" r="10.5" fill="none" stroke="#ccc"/><path d="M6.5 11l3 3 6-6" stroke="#333" stroke-width="1.4" fill="none"/></svg>S</div>
  <div class="abs size" style="left:874px"><b></b>M</div>
  <div class="abs size" style="left:943px"><b></b>L</div>
  <div class="abs size" style="left:1012px"><b></b>XL</div>
  <div class="abs clear">CLEAR</div>

  <div class="abs qty">1<span style="top:0">+</span><span style="top:16px;border-top:1px solid #ccc">-</span></div>
  <a class="abs btn add" href="#">ADD TO CART</a>
  <a class="abs btn buy" href="#">BUY NOW</a>
  <div class="abs share" aria-label="Share"><i></i><i></i><i></i><i></i></div>
</section>

<section class="reviews">
  <div class="abs tab off" style="left:118px">Description</div>
  <div class="abs tab" style="left:320px">Reviews (1)</div>

  <div class="abs h-sm" style="left:121px;top:952px">Based On 1 Reviews</div>
  <div class="abs score">5.00<small>Overall</small></div>

  <div class="abs row" style="top:1031px"><span class="stars">★★★★★</span><div class="bar"><div class="fill" style="width:100%"></div></div><span class="pct">100%</span></div>
  <div class="abs row" style="top:1061px"><span class="stars">★★★★☆</span><div class="bar"></div><span class="pct">&nbsp;&nbsp;0%</span></div>
  <div class="abs row" style="top:1091px"><span class="stars">★★★☆☆</span><div class="bar"></div><span class="pct">&nbsp;&nbsp;0%</span></div>
  <div class="abs row" style="top:1121px"><span class="stars">★★☆☆☆</span><div class="bar"></div><span class="pct">&nbsp;&nbsp;0%</span></div>
  <div class="abs row" style="top:1151px"><span class="stars">★☆☆☆☆</span><div class="bar"></div><span class="pct">&nbsp;&nbsp;0%</span></div>

  <div class="abs h-sm" style="left:658px;top:952px">Add A Review</div>
  <p class="abs note">You must be <a href="#">logged in</a> to post a review.</p>

  <div class="abs h-sm" style="left:126px;top:1224px">1 Review For Colorful Jacket</div>
  <div class="abs avatar" aria-hidden="true"></div>
  <div class="abs stars" style="left:196px;top:1266px;font-size:13px">★★★★★</div>
  <div class="abs" style="left:196px;top:1291px;font-size:12px;color:#555"><b style="font-weight:500;color:#222">Client Name</b> – January 14, 2020:</div>
  <p class="abs review-body">Lorem Ipsum is simply dummy text of the printing and typesetting industry. Lorem Ipsum has been the industry's standard dummy text ever since the 1500s, when an unknown printer took a galley of type and scrambled it to make a type specimen book. It has survived not only five centuries,</p>
</section>

<section class="related-products">
  <h2 class="abs related">Related Products</h2>
  <svg class="abs" style="left:1026px;top:1472px" width="50" height="22"><path d="M9 2l-7 9 7 9" stroke="#888" stroke-width="1.6" fill="none"/><path d="M39 2l7 9-7 9" stroke="#00aeef" stroke-width="1.8" fill="none"/></svg>

  <div class="abs card" style="left:120px">
    <div class="art" role="img" aria-label="Black t-shirt with blue and white lettering print" style="background:#111"></div>
    <div class="nm">Product Name</div><div class="stars">★★★☆☆</div><div class="pr">$120.00</div>
  </div>
  <div class="abs card hover" style="left:367px">
    <div class="art" role="img" aria-label="Black t-shirt with blue chest print" style="background:#111"></div>
    <span class="ring" style="top:22px"></span><span class="ring" style="top:76px"></span><span class="ring solid" style="top:130px"></span>
    <div class="nm">Product Name</div><div class="stars">★★★★☆</div><div class="pr">$120.00</div>
  </div>
  <div class="abs card" style="left:613px">
    <div class="art" role="img" aria-label="White t-shirts, front and back, with heart print" style="background:#e4e4e4"></div>
    <div class="nm">Product Name</div><div class="stars">★★★★★</div><div class="pr">$120.00</div>
  </div>
  <div class="abs card" style="left:860px">
    <div class="art" role="img" aria-label="Black t-shirt with purple chest print" style="background:#111"></div>
    <div class="nm">Product Name</div><div class="stars">★★★★☆</div><div class="pr">$120.00</div>
  </div>
</section>

<footer>
  <div class="abs foot"></div>
  <div class="abs final">ALL SALES FINAL, NO REFUNDS,<br>RETURNS OR EXCHANGES</div>
  <div class="abs" style="left:115px;top:2035px;width:193px;height:1px;background:#444"></div>
  <div class="abs f-txt" style="left:118px;top:2048px">+xxx xxxx xxxxx<br>xxxxxxx@lanternmail.com</div>
  <div class="abs vline" style="left:325px"></div>
  <div class="abs f-head" style="left:371px;top:1970px">Contact Us</div>
  <div class="abs f-txt" style="left:371px;top:2006px;line-height:23px">Home<br>About<br>Services<br>Contact</div>
  <div class="abs vline" style="left:477px"></div>
  <div class="abs f-head" style="left:522px;top:1962px">Email Newsletter</div>
  <div class="abs f-txt" style="left:522px;top:1990px">Sale upto 20 % off for your next purchase inthis month!</div>
  <div class="abs email-box"><span>Email address</span><b>Subscribe</b></div>
  <div class="abs socials" aria-label="Social links"><i></i><i></i><i></i><i></i><i></i></div>
  <div class="abs vline" style="left:905px"></div>
  <div class="abs f-brand">Under Morning Lantern</div>
  <a class="abs btn f-track" href="#">Track Order</a>

  <div class="abs foot-bottom"></div>
  <div class="abs copy">© 2020 Under Morning Lantern &nbsp;| All Rights Reserved</div>
  <div class="abs pay" style="left:738px">Palo</div>
  <div class="abs pay" style="left:797px">Ringcard</div>
  <div class="abs pay" style="left:857px;font-size:8.5px">Amberline</div>
  <div class="abs pay" style="left:916px">PeerPay</div>
  <div class="abs pay" style="left:975px;font-size:9px">Dinerway</div>
  <div class="abs pay" style="left:1034px;font-size:9px">Wayfarer</div>
</footer>

</body>
</html>
```